Australian Trucking Company Requires Professional Looking Stationary

We require a professional looking stationary design that incorporates our newly designed logo.

Our business, called "Brell Haulage Contracting", provides contracting work, transport and logistics to business in Western Australia particularly with links to the mining sector.

We are a small business looking to expand and our new logo and our new stationary will help develop our brand image in our market place.

Target Market(s)

Businesses and Corporation with links to the Mining Sector

Industry/Entity Type

Small Business

Requirements
Must have
• The letterhead must have the following details:
The new logo

Text saying: "Brell Holdings Pty Ltd (ACN 582 316 907) ATF The Brell Discretionary Trust T/AS"
"ABN 71 834 209 553"
Address "P.O Box 817 Wattlegrove WA, 6958"
Phone: 08 9352 7140
Email: brellhaul@mailbox-example.com.au

The text on the letterhead should be editable as the details are likely to change in the near future. Provision should be made for a website address all though one isn't available at the moment.

The styling, layout and font text is entirely up to the designer.

```html
<!DOCTYPE html>
<html lang="en">
<head>
<meta charset="utf-8">
<title>Brell Haulage Contracting – Business Cards</title>
<link rel="stylesheet" href="https://fonts.googleapis.com/css2?family=Open+Sans:wght@400;600;700;800&display=swap">
<style>
  :root {
    --bg: #ebe8e3;
    --white: #ffffff;
    --red: #e01b24;
    --red-deep: #8c0b12;
    --brand-red: #a3121b;
    --grey-light: #e6e6e6;
    --grey: #d4d4d5;
    --text: #3a3a3a;
  }
  * { margin: 0; padding: 0; box-sizing: border-box; }
  html, body { width: 1200px; height: 772px; overflow: hidden; }
  body {
    background: var(--bg);
    font-family: "Open Sans", Arial, sans-serif;
    position: relative;
  }
  .card {
    position: absolute;
    width: 524px;
    height: 298px;
    overflow: hidden;
    background: var(--white);
    box-shadow: 2px 3px 6px rgba(0,0,0,.35);
  }
  .card--front-white { left: 53px; top: 55px; }
  .card--front-grey { left: 623px; top: 55px; }
  .card--back { left: 338px; top: 419px; background: radial-gradient(ellipse at 50% 40%, #e3222b 0%, #b7121a 45%, var(--red-deep) 100%); }

  .brand {
    position: absolute;
    display: flex;
    align-items: center;
    gap: 16px;
  }
  .brand__mark { width: 54px; height: 54px; border-radius: 50%; background: #5a5a5a; flex: none; }
  .brand__name {
    color: var(--brand-red);
    font-weight: 800;
    font-size: 24px;
    line-height: 28px;
    text-transform: uppercase;
    letter-spacing: .5px;
  }
  .card--front-white .brand { left: 92px; top: 64px; }
  .card--front-grey .brand { left: 92px; top: 64px; }

  .legal {
    position: absolute;
    left: 0; right: 0;
    text-align: center;
    font-size: 11px;
    color: var(--text);
  }
  .card--front-white .legal { top: 164px; }
  .card--front-grey .legal { top: 187px; height: 20px; line-height: 20px; background: var(--white); }

  .grey-panel { position: absolute; top: 0; height: 187px; }
  .grey-panel--left { left: 0; width: 195px; background: var(--grey-light); }
  .grey-panel--right { left: 198px; right: 0; background: var(--grey); }

  .contact-band {
    position: absolute;
    left: 0; right: 0; bottom: 0;
    height: 91px;
    background: linear-gradient(90deg, var(--red-deep) 0%, #c3161e 40%, var(--red) 100%);
    color: var(--white);
  }
  .card--front-grey .contact-band { height: 91px; }
  .contact-band__divider {
    position: absolute; left: 196px; top: 0; bottom: 0; width: 2px; background: var(--white);
  }
  .person { position: absolute; right: 344px; top: 32px; text-align: right; }
  .person__name { font-size: 16px; font-weight: 700; }
  .person__title { font-size: 12px; font-weight: 400; }
  .person__abn { font-size: 11.5px; margin-top: 12px; }

  .details { position: absolute; left: 210px; top: 8px; list-style: none; font-size: 11.5px; }
  .details li { display: flex; align-items: center; height: 17px; }
  .details li.gap { margin-bottom: 7px; }
  .details svg { width: 10px; height: 10px; margin-right: 9px; fill: var(--white); flex: none; }

  .back-brand {
    position: absolute; left: 0; right: 0; top: 96px;
    display: flex; align-items: center; justify-content: center; gap: 14px;
  }
  .back-brand__mark { width: 62px; height: 62px; border-radius: 50%; background: var(--white); }
  .back-brand__name { color: var(--white); font-weight: 800; font-size: 22px; line-height: 26px; text-transform: uppercase; }
  .back-web {
    position: absolute; left: 0; right: 0; bottom: 13px; text-align: center;
    color: var(--white); font-size: 13px; font-weight: 700; letter-spacing: 2px;
  }
</style>
</head>
<body>

<section class="card card--front-white">
  <div class="brand">
    <span class="brand__mark"></span>
    <span class="brand__name">Brell<br>Haulage<br>Contracting</span>
  </div>
  <p class="legal">Brell Holdings Pty Ltd (ACN 582 316 907) ATF The Brell Discretionary Trust T/AS</p>
  <div class="contact-band">
    <div class="person">
      <div class="person__name">Your Name <span class="person__title">/ Title</span></div>
      <div class="person__abn">ABN 71 834 209 553</div>
    </div>
    <span class="contact-band__divider"></span>
    <ul class="details">
      <li class="gap"><svg viewBox="0 0 10 10"><path d="M5 0 10 5H8.5V10H6V7H4V10H1.5V5H0Z"/></svg>P.O Box 817 Wattlegrove WA, 6958</li>
      <li><svg viewBox="0 0 10 10"><path d="M2 0 4 2.5 3 4Q4 6 6 7L7.5 6 10 8 8.5 10Q3 9.5 0 1.5Z"/></svg>08 9352 7140</li>
      <li><svg viewBox="0 0 10 10"><path d="M0 2H10V8H0ZM0 2 5 5.5 10 2" /></svg>brellhaul@mailbox-example.com.au</li>
      <li><svg viewBox="0 0 10 10"><circle cx="5" cy="5" r="5"/></svg>www.brellhaul-example.com</li>
    </ul>
  </div>
</section>

<section class="card card--front-grey">
  <div class="grey-panel grey-panel--left"></div>
  <div class="grey-panel grey-panel--right"></div>
  <div class="brand">
    <span class="brand__mark"></span>
    <span class="brand__name">Brell<br>Haulage<br>Contracting</span>
  </div>
  <p class="legal">Brell Holdings Pty Ltd (ACN 582 316 907) ATF The Brell Discretionary Trust T/AS</p>
  <div class="contact-band">
    <div class="person">
      <div class="person__name">Your Name <span class="person__title">/ Title</span></div>
      <div class="person__abn">ABN 71 834 209 553</div>
    </div>
    <span class="contact-band__divider"></span>
    <ul class="details">
      <li class="gap"><svg viewBox="0 0 10 10"><path d="M5 0 10 5H8.5V10H6V7H4V10H1.5V5H0Z"/></svg>P.O Box 817 Wattlegrove WA, 6958</li>
      <li><svg viewBox="0 0 10 10"><path d="M2 0 4 2.5 3 4Q4 6 6 7L7.5 6 10 8 8.5 10Q3 9.5 0 1.5Z"/></svg>08 9352 7140</li>
      <li><svg viewBox="0 0 10 10"><path d="M0 2H10V8H0ZM0 2 5 5.5 10 2" /></svg>brellhaul@mailbox-example.com.au</li>
      <li><svg viewBox="0 0 10 10"><circle cx="5" cy="5" r="5"/></svg>www.brellhaul-example.com</li>
    </ul>
  </div>
</section>

<section class="card card--back">
  <div class="back-brand">
    <span class="back-brand__mark"></span>
    <span class="back-brand__name">Brell<br>Haulage<br>Contracting</span>
  </div>
  <p class="back-web">www.brellhaul-example.com</p>
</section>

</body>
</html>
```